Flyer für Verkauf von Radondetektoren
Zielgruppe
Ich verkaufe Radondetektoren zur Messung von Radon in Innenräumen. Zielgruppe sind Privatpersonen, Firmen, Genossenschaften und andere Hauseigentümer.
Aufgabenstellung
Ich brauche das Design für meine Messanleitung.
Kreativ - modern - weniger kann mehr sein
Struktur ist wichtigt, es soll also einfach sein zu lesen und zu verstehen, was gemacht werden soll. Können Bulletpoints, Icons mit eingebracht werden.
Wichtig ist auch, dass die beiden Logos 'Luftprüfer.de' und TESTOVAL' auf der Messanleitung vorhanden sind. Wobei 'Luftprüfer.de' das Hauptlogo ist.
DIN format dachte ich A4 beidseitig (Text müsste also auf diese Grösse angepasst werden).
Kann natürlich auch Flyer-Format sein oder andere Vorschläge!
Bildmaterial gibt es auf unsere Homepage https://luftprüfer.de und https://luftkontroll.se . Diese haben wir bereits gekauft und können verwendet werden. Ich lade sie den bei Bedarf hoch. Es können natürlich auch andere Vorschläge kommen.

```html
<!DOCTYPE html>
<html lang="de">
<head>
<meta charset="utf-8">
<title>Messanleitung – Luftprüfer.de</title>
<link href="https://fonts.googleapis.com/css2?family=Roboto:ital,wght@0,300;0,400;0,500;0,700;1,400;1,700&family=Roboto+Condensed:wght@400;700&display=swap" rel="stylesheet">
<style>
:root{
  --red:#d7262f;
  --dark:#3a3a3a;
  --text:#4a4a4a;
  --grey:#e6e6e6;
  --grey-2:#d5d5d5;
  --paper:#ffffff;
  --bg:#ebe7e2;
}
*{box-sizing:border-box;margin:0;padding:0}
html,body{width:1200px;height:1153px;overflow:hidden}
body{background:var(--bg);font-family:"Roboto",sans-serif;color:var(--text)}
.sheet{position:absolute;left:20px;width:1160px;height:545px;display:grid;grid-template-columns:repeat(3,1fr);box-shadow:0 4px 14px rgba(0,0,0,.15)}
.sheet--outside{top:18px}
.sheet--inside{top:588px}
.panel{position:relative;overflow:hidden;background:var(--paper);padding:0 22px 0 22px;font-size:8.3px;line-height:1.45}
.panel--grey{background:linear-gradient(180deg,#f1f1f1,#e2e2e2)}
.step-bar{margin:22px -22px 0 0;height:40px;background:linear-gradient(90deg,#dcdcdc,#c9c9c9);display:flex;align-items:center;padding-left:0;position:relative}
.panel .step-bar{margin-left:-22px;padding-left:22px}
.step-bar b{font-size:19px;color:var(--dark);margin-right:5px}
.step-bar span{font-size:13px;letter-spacing:1px;color:var(--dark)}
.step-icon{position:absolute;right:20px;top:-3px;width:46px;height:46px;border-radius:50%;background:var(--red);border:3px solid #fff;display:flex;align-items:center;justify-content:center}
h2{font-family:"Roboto",sans-serif;font-weight:700;font-size:19px;letter-spacing:.8px;color:var(--dark);line-height:1.15;margin:30px 0 10px}
h3{font-size:11px;font-weight:700;color:var(--red);display:flex;align-items:center;gap:7px;margin:16px 0 8px;line-height:1.2}
p{margin-bottom:7px}
.bullets{list-style:none}
.bullets li{position:relative;padding-left:13px;margin-bottom:2px}
.bullets li::before{content:"»";position:absolute;left:0;top:-1px;font-weight:700;font-size:10px;color:var(--dark)}
.dots{list-style:none}
.dots li{position:relative;padding-left:8px}
.dots li::before{content:"•";position:absolute;left:0}
.note{display:flex;align-items:center;gap:8px;font-style:italic;font-weight:700;color:var(--dark);font-size:10.5px;line-height:1.35;margin:8px 0}
.small-title{font-style:italic;font-weight:700;margin-top:10px}
.address{display:flex;gap:10px;align-items:center;color:var(--red);margin:14px 0;font-size:8.5px;line-height:1.4}
.address strong{font-weight:500}
.partner{position:absolute;left:22px;bottom:22px;display:flex;align-items:center;gap:8px;font-size:22px;font-weight:500;color:#1f4c8f;letter-spacing:1px}
.partner i{width:18px;height:18px;border-radius:50%;background:#1f4c8f;display:block}
.cover-image{height:272px;margin:0 -22px;background:linear-gradient(180deg,#ffffff 0%,#cfe3f0 30%,#8a78b0 48%,#5fa34a 68%,#e3a53a 85%,#4f9a3e 100%)}
.cover-body{background:linear-gradient(180deg,#d8d8d8,#f4f4f4 70%);margin:0 -22px;padding:16px 22px 0;height:240px;position:relative}
.cover-body h1{font-size:28px;font-weight:700;letter-spacing:1px;color:var(--dark);line-height:1}
.cover-body .sub{font-size:13px;line-height:1.45;color:var(--dark);margin-top:6px}
.product{position:absolute;right:18px;top:104px;width:150px;height:72px;border-radius:40px;background:radial-gradient(ellipse at 60% 40%,#555,#1d1d1d 70%)}
.brand{position:absolute;left:22px;bottom:18px;display:flex;align-items:center;gap:8px;font-size:23px;color:var(--dark)}
.brand i{width:20px;height:20px;border-radius:50%;background:#f0c419;display:block}
.red-foot{position:absolute;left:0;right:0;bottom:0;height:10px;background:var(--red)}
.url-button{display:inline-block;background:var(--red);color:#fff;font-weight:500;font-size:10.5px;padding:7px 14px;border-radius:16px;margin:6px 0 14px}
.hint{font-style:italic}
.contact-band{position:absolute;left:386px;right:0;bottom:0;height:68px;background:var(--red);color:#fff;display:flex;align-items:center;gap:16px;padding-left:20px;font-style:italic;font-size:10.5px;line-height:1.45;font-weight:700}
.contact-band span{font-weight:400}
</style>
</head>
<body>

<!-- Outside: Schritt 3, Schritt 4, Titel -->
<section class="sheet sheet--outside">
  <article class="panel">
    <div class="step-bar"><b>3.</b><span>SCHRITT</span>
      <div class="step-icon"><svg width="24" height="24" viewBox="0 0 24 24" fill="none" stroke="#fff" stroke-width="2"><circle cx="12" cy="13" r="8"/><path d="M12 13V8M12 13l4 2M10 3h4"/></svg></div>
    </div>
    <h2>RADONMESSUNG</h2>
    <p>Die Radonmessung beginnt, sobald Sie die radondichten Verpackungen öffnen.</p>
    <div class="note"><svg width="28" height="28" viewBox="0 0 28 28" fill="none" stroke="var(--red)" stroke-width="2.5"><rect x="2" y="6" width="20" height="20" rx="2"/><path d="M7 15l5 5L26 3"/></svg>Bitte halten Sie die Messdauer<br>wie folgt ein:</div>
    <h3><svg width="26" height="26" viewBox="0 0 26 26" fill="none" stroke="var(--red)" stroke-width="1.6"><circle cx="13" cy="14" r="10"/><path d="M13 14V8M10 2h6"/></svg>Kurzzeitmessung</h3>
    <ul class="bullets">
      <li>Mindestmessdauer 10 Tage (bis hin zu 30 Tagen).</li>
      <li>Führen Sie die Messung vorzugsweise in der Heizperiode (1. Oktober – 30. April) durch.</li>
      <li>Kurzzeitmessungen werden oft beim Kauf oder Verkauf von Immobilien genutzt, um ein mögliches Gefährdungspotential abschätzen zu können, oder wenn die Zeit nicht ausreicht, um eine Langzeitmessung durchzuführen.</li>
    </ul>
    <h3><svg width="26" height="26" viewBox="0 0 26 26" fill="none" stroke="var(--red)" stroke-width="1.6"><circle cx="13" cy="14" r="10"/><path d="M13 14V8M10 2h6M13 14l5 3"/></svg>Langzeitmessung</h3>
    <ul class="bullets">
      <li>Mindestmessdauer 3 Monate während der Heizperiode (1. Oktober – 30. April).</li>
      <li>Um einen Jahresmittelwert der Radonkonzentration in Innenräumen ermitteln zu können, halten Sie die Messdauer von 12 Monaten ein.</li>
      <li>Falls Ihr Arbeitsplatz in einem Radon-Vorsorgegebiet liegt und somit der Messpflicht unterliegt, muss die Messdauer von 12 Monaten eingehalten werden.</li>
    </ul>
  </article>

  <article class="panel panel--grey">
    <div class="step-bar"><b>4.</b><span>SCHRITT</span>
      <div class="step-icon"><svg width="24" height="24" viewBox="0 0 24 24" fill="#fff"><rect x="4" y="12" width="3" height="7"/><rect x="9" y="8" width="3" height="11"/><rect x="14" y="10" width="3" height="9"/><rect x="3" y="20" width="18" height="1.5"/></svg></div>
    </div>
    <h2>AUSWERTUNG<br>UND PRÜFBERICHT</h2>
    <p>Nach Ablauf der Messdauer, loggen Sie sich wieder auf <b>https://kunden.testoval.se/de</b> in Ihrem Account ein. Vermerken Sie hier das Ende der Messung und senden Sie anschließend alle Radondetektoren ausreichend frankiert in einem Umschlag oder einem Karton zeitnah an unsere Rücksendeadresse:</p>
    <div class="address"><svg width="28" height="20" viewBox="0 0 28 20" fill="none" stroke="var(--red)" stroke-width="1.6"><rect x="1" y="1" width="26" height="18"/><path d="M1 1l13 10L27 1M1 19l10-9M27 19l-10-9"/></svg><div><strong>Luftprüfer.de</strong><br>Lindenring 14, 28195 Musterhafen</div></div>
    <p>Sobald die Radondetektoren im Labor von TESTOVAL eingetroffen sind, werden diese fachgerecht analysiert und die Ergebnisse der Radonmessung ausgewertet. Ein vollständiger Prüfbericht wird Ihnen innerhalb 36 Stunden nach Erhalt der Detektoren im Labor per E-Mail zugeschickt.</p>
    <p class="small-title">Weitere Hinweise</p>
    <ul class="dots" style="font-size:7.4px;line-height:1.4">
      <li>Bitte beachten Sie, dass die Radonmessung innerhalb von 15 Monaten nach Kaufdatum abgeschlossen sein muss.</li>
      <li>Versuchen Sie nicht das Gehäuse der Detektoren zu öffnen und platzieren Sie diese immer außer Reichweite von Kindern.</li>
      <li>Während der gesamten Messdauer dürfen die Detektoren nicht an einem anderen Ort umplatziert werden.</li>
      <li>Durch die Anmeldung auf der Website https://kunden.testoval.se/de und die Eingabe der erforderlichen Daten bestätigt der/die Wohnungseigentümer*in/Messverantwortliche, dass er/sie die Messanleitung befolgt hat und die Detektoren gemäß den Anweisungen korrekt platziert wurden.</li>
    </ul>
    <p class="small-title" style="margin-top:8px;font-size:7.4px">Datenschutz (GDPR), Impressum und AGBs</p>
    <p style="font-size:7.4px;line-height:1.4">Mehr Information dazu finden Sie unter www.luftprüfer.de<br>Copyright © 2023 Nordluft Mätteknik AB<br>Alle Rechte vorbehalten www.luftprüfer.de</p>
    <div class="partner"><i></i>TESTOVAL</div>
  </article>

  <article class="panel">
    <div class="cover-image" role="img" aria-label="Illustration: Stadtsilhouette mit grünen Hügeln und Wohnhäusern"></div>
    <div class="cover-body">
      <h1>MESSANLEITUNG</h1>
      <p class="sub">für Radonmessungen<br>von Innenraumluft<br>mit passiven Radon Detektoren</p>
      <div class="product" role="img" aria-label="Foto: zwei schwarze passive Radondetektoren"></div>
      <div class="brand"><i></i>Luftprüfer.de</div>
    </div>
    <div class="red-foot"></div>
  </article>
</section>

<!-- Inside: Schritt 1 & 2, Auswahl der Räume, Arbeitsplätze -->
<section class="sheet sheet--inside">
  <article class="panel panel--grey">
    <div class="step-bar"><b>1.</b><span>SCHRITT</span>
      <div class="step-icon"><svg width="24" height="24" viewBox="0 0 24 24" fill="#fff"><circle cx="10" cy="8" r="4"/><path d="M3 20c0-5 3-7 7-7s7 2 7 7z"/><circle cx="18" cy="15" r="3" fill="none" stroke="#fff" stroke-width="1.6"/></svg></div>
    </div>
    <h2 style="margin-top:14px">REGISTRIERUNG<br>UND ANMELDUNG</h2>
    <p>Wenn Sie Neukunde sind, legen Sie bitte zunächst ein neues Benutzerkonto auf unserem Online-Portal an:</p>
    <span class="url-button">https://kunden.testoval.se/de</span>
    <p>Anschließend können Sie die Radondetektoren registrieren. Vermerken Sie den Start der Messung (Datum und Uhrzeit), die Messorte (Raum und Etage) sowie die 9-stellige Seriennummer der Detektoren, die Sie auf der Verpackung oder auf der Unterseite der jeweiligen Detektoren finden.</p>
    <p class="hint">Firmenkunden haben die Möglichkeit eine Excel-Datei als Hilfsmittel herunterzuladen, die Sie ausfüllen und dann wieder hochladen.</p>
    <div class="step-bar" style="margin-top:14px"><b>2.</b><span>SCHRITT</span>
      <div class="step-icon"><svg width="22" height="22" viewBox="0 0 24 24" fill="#fff"><path d="M12 2a7 7 0 0 0-7 7c0 5 7 13 7 13s7-8 7-13a7 7 0 0 0-7-7z"/><circle cx="12" cy="9" r="2.6" fill="var(--red)"/></svg></div>
    </div>
    <h2 style="margin-top:14px">PLATZIERUNG<br>DER DETEKTOREN</h2>
    <p>Bevor Sie die Detektoren der Verpackung entnehmen, überlegen Sie wo genau Sie die Radondetektoren platzieren wollen. Die Radonmessung beginnt, sobald Sie die radondichten Verpackungen öffnen. Beachten Sie bei der Platzierung zunächst die Auswahl der Räume und die Positionierung der Radondetektoren im Raum.</p>
  </article>

  <article class="panel">
    <div class="note" style="margin-top:26px"><svg width="28" height="28" viewBox="0 0 28 28" fill="none" stroke="var(--red)" stroke-width="2.5"><rect x="2" y="6" width="20" height="20" rx="2"/><path d="M7 15l5 5L26 3"/></svg>Für eine zuverlässige Radonmessung<br>empfehlen wir wie folgt vorzugehen:</div>
    <h2 style="margin-top:20px">AUSWAHL DER RÄUME</h2>
    <h3><svg width="24" height="22" viewBox="0 0 24 22" fill="var(--red)"><path d="M12 1L1 10h3v11h16V10h3z"/><rect x="9" y="13" width="6" height="8" fill="#fff"/></svg>Einfamilienhäuser</h3>
    <ul class="bullets">
      <li>Es sollten mindestens zwei Wohnräume und pro bewohnte Etage mindestens ein Wohnraum gemessen werden. Wählen Sie Räume aus, in denen Sie sich oft aufhalten (z.B. das Wohn- und Schlafzimmer). Vermeiden Sie aber Räume, in denen das Fenster mehrere Stunden am Tag oder in der Nacht geöffnet ist.</li>
      <li>Insofern Sie einen Keller haben, empfehlen wir alle Kellerräume zu messen, da hier meist das größte Risiko einer erhöhten Radonkonzentration erwartet wird.</li>
    </ul>
    <h3><svg width="24" height="30" viewBox="0 0 24 30" fill="var(--red)"><path d="M12 1L1 8v21h22V8z"/><g fill="#fff"><rect x="6" y="11" width="4" height="4"/><rect x="14" y="11" width="4" height="4"/><rect x="6" y="18" width="4" height="4"/><rect x="14" y="18" width="4" height="4"/></g></svg>Mehrfamilienhäuser, Wohnungen<br>und Wohnkomplexen</h3>
    <ul class="bullets">
      <li>Alle Wohnungen mit direktem Bodenkontakt sowie mindestens eine Wohnung pro Etage sollten gemessen werden. Wählen Sie dabei Wohnungen, die an Aufzügen oder Luftschächten liegen.</li>
      <li>In größeren Wohnkomplexen sollten insgesamt mindestens 20 % aller Wohnungen in einem Gebäude gemessen werden.</li>
      <li>Es sollten mindestens zwei Wohnräume pro ausgewählte Wohnung gemessen werden. Wählen Sie Räume aus, in denen Sie sich oft aufhalten (z.B. das Wohn- und Schlafzimmer). Vermeiden Sie aber Räume, in denen das Fenster mehrere Stunden am Tag oder in der Nacht geöffnet ist.</li>
      <li>Selbst bei einer Einzimmerwohnung sollten Sie zwei Detektoren aufstellen.</li>
    </ul>
  </article>

  <article class="panel">
    <h3 style="margin-top:30px"><svg width="24" height="32" viewBox="0 0 24 32" fill="var(--red)"><rect x="1" y="1" width="22" height="30"/><g fill="#fff"><rect x="5" y="6" width="4" height="4"/><rect x="15" y="6" width="4" height="4"/><rect x="5" y="13" width="4" height="4"/><rect x="15" y="13" width="4" height="4"/><rect x="5" y="20" width="4" height="4"/><rect x="15" y="20" width="4" height="4"/></g></svg>Arbeitsplätze und öffentliche Gebäude</h3>
    <ul class="bullets">
      <li>Wählen Sie Räume, die regelmäßig mehr als vier Stunden pro Tag genutzt werden.</li>
      <li>Messen Sie alle unterirdischen Räumlichkeiten, da hier meist das größte Risiko einer erhöhten Radonkonzentration erwartet wird.</li>
      <li>Messen Sie alle Räume im Erdgeschoß. Für größere Räumlichkeiten empfehlen wir einen Detektor pro 200 m².</li>
      <li>In den oberen Etagen sollten Sie mit mindestens zwei Detektoren, sowie mindestens einem Detektor pro 200 m² messen.</li>
      <li>Falls Ihr Arbeitsplatz in einem Radon-Vorsorgegebiet liegt und somit der Messpflicht unterliegt, muss die Messdauer von 12 Monaten eingehalten werden.</li>
    </ul>
    <h3 style="margin-top:18px"><svg width="28" height="22" viewBox="0 0 28 22" fill="none" stroke="var(--red)" stroke-width="1.8"><rect x="1" y="1" width="26" height="20"/><rect x="6" y="6" width="16" height="8"/></svg>Platzierung der Detektoren im Raum</h3>
    <ul class="bullets">
      <li>Platzieren Sie die Detektoren in einem Mindestabstand von 20 cm zu Wänden, 50 cm zu Abluftsventilen, sowie 1,50 m zu Fenstern, Außentüren, Zuluftsventilen und Heizkörpern.</li>
      <li>Stellen Sie die Detektoren nicht auf dem Boden, an starken Wärmequellen oder Luftströmen auf. Vermeiden Sie auch Räume mit hoher Luftfeuchtigkeit, wie zum Beispiel das Badezimmer.</li>
      <li>Die Detektoren können entweder stehend (auf einem Tisch, im Regal oder einer Schrankwand) oder hängend mitten im Raum (z.B. von einer Lampe) platziert werden.</li>
      <li>Stellen Sie die Detektoren während der gesamten Messdauer nicht um.</li>
      <li>Versuchen Sie nicht das Gehäuse der Detektoren zu öffnen und platzieren Sie diese immer außer Reichweite von Kindern.</li>
    </ul>
  </article>

  <div class="contact-band">
    <svg width="40" height="40" viewBox="0 0 40 40" fill="none" stroke="#fff" stroke-width="1.8"><path d="M3 4h34v24H18l-8 8v-8H3z"/><circle cx="14" cy="14" r="1" fill="#fff"/><circle cx="26" cy="14" r="1" fill="#fff"/><path d="M14 20q6 4 12 0"/></svg>
    <div>Wenn Sie noch Fragen haben, rufen Sie uns an. Wir sind Ihnen gern behilflich.<br>Telefon +49 (0) 151 234 567 89 <span>Mo - Fr / 13 - 15 Uhr</span></div>
  </div>
</section>

</body>
</html>
```